Velvet Lantern rebranding my business with a new business card

I have my new logo and now I need a refresher on my business cards. I really want something fun and fresh. I like black background or anything to make the color pop.
Logo
Name: Velvet Lantern
Contact Info as stated below:
Mira Pellow
555-013-4762
Logo
Name: Velvet Lantern
Mira Pellow
555-013-4762
fb.me/VelvetLanternbyMira
Instagram: @VelvetLanternbyMira

Industry/Entity Type

Business

Contact Information for Business Card

double-sided. Logo on one side. Contact info on the other.

Requirements
Must have
• Logo
• Name: Velvet Lantern
• Contact Info as stated below:
• Mira Pellow
• 555-013-4762
• fb.me/VelvetLanternbyMira
• fb.me/VelvetLanternbyMira

```html
<!DOCTYPE html>
<html lang="en">
<head>
<meta charset="utf-8">
<title>Velvet Lantern — Business Card</title>
<link rel="stylesheet" href="https://fonts.googleapis.com/css2?family=Oswald:wght@500&family=Roboto:wght@300;400&display=swap">
<style>
  :root {
    --backdrop: #2b2b2d;
    --card-dark: #1c1c1d;
    --card-light: #f4f4f3;
    --ink-dark: #1e1e1e;
    --ink-muted: #4a4a4a;
    --ink-light: #e9e9e9;
    --badge-fill: #ffffff;
    --badge-ring: #f2b8c6;
    --divider: #b9b9b9;
  }
  * { box-sizing: border-box; margin: 0; padding: 0; }
  html, body { width: 1200px; height: 900px; overflow: hidden; }
  body {
    background: var(--backdrop);
    display: flex;
    flex-direction: column;
    align-items: center;
    justify-content: center;
    gap: 50px;
    font-family: "Roboto", Arial, sans-serif;
  }
  .card {
    width: 630px;
    height: 360px;
    position: relative;
    box-shadow: 0 10px 24px rgba(0,0,0,0.35);
  }
  .card--front {
    background: var(--card-dark);
    display: flex;
    flex-direction: column;
    align-items: center;
    justify-content: center;
    gap: 26px;
  }
  .brand-badge {
    width: 190px;
    height: 190px;
    border-radius: 50%;
    background: var(--badge-fill);
    border: 6px solid var(--badge-ring);
    display: flex;
    align-items: center;
    justify-content: center;
    text-align: center;
  }
  .brand-name {
    font-family: "Roboto", Arial, sans-serif;
    font-weight: 400;
    font-size: 26px;
    line-height: 1.15;
    color: var(--ink-dark);
  }
  .front-url {
    color: var(--ink-light);
    font-weight: 300;
    font-size: 15px;
    letter-spacing: 0.55em;
    margin-right: -0.55em;
  }
  .card--back {
    background: var(--card-light);
    display: flex;
    align-items: center;
    padding-left: 120px;
    padding-top: 20px;
  }
  .holder-name {
    font-family: "Oswald", "Arial Narrow", sans-serif;
    font-weight: 500;
    font-size: 34px;
    letter-spacing: 0.01em;
    color: var(--ink-dark);
    text-transform: uppercase;
  }
  .divider {
    width: 1px;
    height: 78px;
    background: var(--divider);
    margin: 0 22px 0 26px;
  }
  .contact-list { list-style: none; }
  .contact-item {
    display: flex;
    align-items: center;
    gap: 10px;
    font-size: 17px;
    line-height: 1.35;
    color: var(--ink-muted);
  }
  .contact-icon { width: 13px; height: 13px; flex: none; fill: var(--ink-dark); }
</style>
</head>
<body>
  <section class="card card--front" aria-label="Card front">
    <div class="brand-badge">
      <span class="brand-name">Velvet<br>Lantern</span>
    </div>
    <p class="front-url">www.velvetlantern.com</p>
  </section>

  <section class="card card--back" aria-label="Card back">
    <h1 class="holder-name">Mira Pellow</h1>
    <span class="divider" aria-hidden="true"></span>
    <ul class="contact-list">
      <li class="contact-item">
        <svg class="contact-icon" viewBox="0 0 24 24" aria-hidden="true"><path d="M6.6 10.8a15.2 15.2 0 0 0 6.6 6.6l2.2-2.2a1 1 0 0 1 1-.25 11.4 11.4 0 0 0 3.6.57 1 1 0 0 1 1 1V20a1 1 0 0 1-1 1A17 17 0 0 1 3 4a1 1 0 0 1 1-1h3.5a1 1 0 0 1 1 1c0 1.25.2 2.46.57 3.6a1 1 0 0 1-.25 1z"/></svg>
        555-013-4762
      </li>
      <li class="contact-item">
        <svg class="contact-icon" viewBox="0 0 24 24" aria-hidden="true"><circle cx="12" cy="12" r="10"/><circle cx="12" cy="12" r="4" fill="#f4f4f3"/></svg>
        www.velvetlantern.com
      </li>
      <li class="contact-item">
        <svg class="contact-icon" viewBox="0 0 24 24" aria-hidden="true"><rect x="2" y="2" width="20" height="20"/></svg>
        fb.me/VelvetLanternbyMira
      </li>
    </ul>
  </section>
</body>
</html>
```